Creation of an elegant and modern turnkey Shopify website

Hello,

We are a new company specializing in the sale of above-ground pools. We want to create a turnkey website, ideally using Shopify. For now, we need a "showcase" site, not an e-commerce platform, with four tabs:

Home Page (an overall presentation of the company)
Our Products (an overview of all the above-ground pools we sell)
Our Projects (a page inspired by Instagram to showcase photos of our future projects)
Contact (a page with all our contact information and a contact form)

We are looking to create a highly visual, elegant, and modern website with vibrant splashes of color. We will provide the text, photos (along with instructions on where to place them on each page), and all other necessary information as attachments.

Thank you in advance for your proposals!

The Brisa Lagoon Team

Target Market(s)

Targeted at Swiss customers (a translator will need to be installed for different languages)

Industry/Entity Type

Sale of customised above-ground pools

Coding

Coded - Design and coding required

Font styles to use
Sans Serif

Colors
0094D4
00A9DD
6FCCEA
C7EBF8
E9F6FB
00AB8E
00BBA5
67D7C9
C6EFE9
E9F9F6

Requirements
Must have
• A stunning, elegant and modern look
Nice to have
• Inspiration from the colors of our logo throughout the site, but in an elegant way
Should not have
• An overly classic look for swimming pool sites

```html
<!DOCTYPE html>
<html lang="en">
<head>
<meta charset="utf-8">
<title>Brisa Lagoon — Above-Ground Pools</title>
<link href="https://fonts.googleapis.com/css2?family=Poppins:wght@300;400;500;700&display=swap" rel="stylesheet">
<style>
:root{
  --blue-deep:#0094D4;
  --blue:#00A9DD;
  --blue-light:#6FCCEA;
  --blue-pale:#C7EBF8;
  --blue-mist:#E9F6FB;
  --page:#f6f6f6;
  --panel:#ffffff;
  --ink:#111111;
  --ink-soft:#5a5a5a;
  --white:#ffffff;
}
*{box-sizing:border-box;margin:0;padding:0}
html,body{width:1200px;height:2656px;overflow:hidden}
body{font-family:"Poppins",sans-serif;background:var(--page);color:var(--ink);position:relative}

.site-header{height:104px;display:flex;align-items:center;justify-content:space-between;padding:0 74px 0 77px;background:var(--page)}
.brand{display:flex;flex-direction:column;line-height:1;font-weight:300;color:var(--blue);font-size:26px;letter-spacing:1px}
.brand span+span{margin-top:4px}
.main-nav{display:flex;gap:21px;font-size:13.5px}
.main-nav a{color:var(--ink);text-decoration:none}

.photo{display:block;width:100%;height:100%}

.range{display:flex;gap:16px;height:380px}
.range-card{position:relative;width:288px;overflow:hidden}
.range-card .label{position:absolute;left:27px;bottom:30px;right:27px;color:var(--white);font-size:21px;line-height:30px}

.split{display:flex;gap:16px;margin-top:17px}
.split .media{width:694px;flex:none}
.split .media.wide{width:693px}
.split .copy{flex:1;background:var(--panel);padding:44px 26px 0 26px}
.split.reverse .copy{flex:none;width:490px}
.split.reverse .media{flex:1;width:auto}

.intro{height:419px}
.intro .copy h1{font-size:36px;font-weight:400;line-height:50px;margin-bottom:22px}
.intro .lead{font-size:13.5px;line-height:20px;margin-bottom:22px}
.body-text{font-size:13.5px;line-height:20px;color:var(--ink-soft)}

.features{display:flex;gap:16px;height:420px;margin-top:17px}
.feature{position:relative;width:227px;overflow:hidden}
.feature .text{position:absolute;left:27px;right:20px;bottom:28px;color:var(--white)}
.feature h3{font-size:21px;font-weight:400;line-height:30px;margin-bottom:9px}
.feature p{font-size:13.5px;line-height:20px}

.block{height:333px}
.block h2{font-size:36px;font-weight:400;line-height:48px;margin-bottom:22px}
.block strong{color:var(--ink);font-weight:700}
.button{display:inline-block;margin-top:26px;background:var(--blue-deep);color:var(--white);font-size:15px;padding:12px 24px;text-decoration:none}

.site-footer{position:absolute;top:2407px;left:0;width:1200px;height:206px;display:flex;flex-direction:column;align-items:center;padding-top:34px}
.site-footer .brand{align-items:center}
.tagline{font-size:13.5px;margin-top:22px}
.socials{display:flex;gap:20px;margin-top:12px}
.socials span{width:20px;height:20px;border-radius:50%;border:2px solid var(--blue-deep)}
.copyright{position:absolute;top:2613px;left:0;width:1200px;height:43px;background:var(--blue-deep);color:var(--white);font-size:13.5px;display:flex;align-items:center;justify-content:center}
</style>
</head>
<body>

<header class="site-header">
  <div class="brand"><span>BRISA</span><span>LAGOON</span></div>
  <nav class="main-nav">
    <a href="#">Home</a><a href="#">Our Product</a><a href="#">Our Project</a><a href="#">Contact</a>
  </nav>
</header>

<section class="range">
  <div class="range-card">
    <svg class="photo" role="img" aria-label="Aluminium pool beside a coastal house" viewBox="0 0 288 380" preserveAspectRatio="none"><defs><linearGradient id="r1" x1="0" y1="0" x2="0" y2="1"><stop offset="0" stop-color="#7d9cbf"/><stop offset=".5" stop-color="#a99f86"/><stop offset=".7" stop-color="#3fa1b4"/><stop offset="1" stop-color="#6cc2cc"/></linearGradient></defs><rect width="288" height="380" fill="url(#r1)"/></svg>
    <div class="label">Aluminium Pools</div>
  </div>
  <div class="range-card">
    <svg class="photo" role="img" aria-label="Above-ground pool framed by palm trees" viewBox="0 0 288 380" preserveAspectRatio="none"><defs><linearGradient id="r2" x1="0" y1="0" x2="0" y2="1"><stop offset="0" stop-color="#5bb7d6"/><stop offset=".45" stop-color="#2f5d4e"/><stop offset=".75" stop-color="#2aa9b5"/><stop offset="1" stop-color="#6fd0d4"/></linearGradient></defs><rect width="288" height="380" fill="url(#r2)"/></svg>
    <div class="label">Above-Ground Pools with Aluminium and Wood</div>
  </div>
  <div class="range-card">
    <svg class="photo" role="img" aria-label="Resort pool with palm trees and wooden deck" viewBox="0 0 288 380" preserveAspectRatio="none"><defs><linearGradient id="r3" x1="0" y1="0" x2="0" y2="1"><stop offset="0" stop-color="#9ec3e0"/><stop offset=".5" stop-color="#5f8c3e"/><stop offset=".8" stop-color="#3eb7c4"/><stop offset="1" stop-color="#78cfd6"/></linearGradient></defs><rect width="288" height="380" fill="url(#r3)"/></svg>
    <div class="label">Galvanized Steel Pools with Composite Wood Coverings</div>
  </div>
  <div class="range-card">
    <svg class="photo" role="img" aria-label="Indoor mini pool spa with blue tiles" viewBox="0 0 288 380" preserveAspectRatio="none"><defs><linearGradient id="r4" x1="0" y1="0" x2="0" y2="1"><stop offset="0" stop-color="#e7dcc8"/><stop offset=".4" stop-color="#c9b89d"/><stop offset=".55" stop-color="#2f86d4"/><stop offset="1" stop-color="#1d6fc0"/></linearGradient></defs><rect width="288" height="380" fill="url(#r4)"/></svg>
    <div class="label">Mini Pool Spa</div>
  </div>
</section>

<section class="split intro">
  <div class="media">
    <svg class="photo" role="img" aria-label="Terrace pool under pine trees overlooking a bay" viewBox="0 0 694 419" preserveAspectRatio="none"><defs><linearGradient id="s1" x1="0" y1="0" x2="0" y2="1"><stop offset="0" stop-color="#5aa9e3"/><stop offset=".45" stop-color="#3f6a3a"/><stop offset=".6" stop-color="#4e86b0"/><stop offset=".8" stop-color="#3fc0dd"/><stop offset="1" stop-color="#8e9c8a"/></linearGradient></defs><rect width="694" height="419" fill="url(#s1)"/></svg>
  </div>
  <div class="copy">
    <h1>Transform Your Garden with Our Premium Above-Ground Pools!</h1>
    <p class="lead">Achieve your dreams with our custom, tailor-made above-ground pools.</p>
    <p class="body-text">Imagine an exceptional relaxation and leisure space right in your own backyard. With our unparalleled expertise and commitment to excellence, we create above-ground pools that exceed all expectations. Our exclusive, custom-designed models are crafted to combine style, durability, and innovation, offering a unique and refined experience.</p>
  </div>
</section>

<section class="features">
  <div class="feature">
    <svg class="photo" role="img" aria-label="Indoor pool with blue mosaic tiles" viewBox="0 0 227 420" preserveAspectRatio="none"><defs><linearGradient id="f1" x1="0" y1="0" x2="0" y2="1"><stop offset="0" stop-color="#e3d6c3"/><stop offset=".3" stop-color="#3b8fd4"/><stop offset="1" stop-color="#1a6cb4"/></linearGradient></defs><rect width="227" height="420" fill="url(#f1)"/></svg>
    <div class="text"><h3>Superior Quality</h3><p>Each pool is constructed with high-quality materials, ensuring exceptional durability and strength.</p></div>
  </div>
  <div class="feature">
    <svg class="photo" role="img" aria-label="Pool surrounded by lush garden trees" viewBox="0 0 227 420" preserveAspectRatio="none"><defs><linearGradient id="f2" x1="0" y1="0" x2="0" y2="1"><stop offset="0" stop-color="#7a9a3a"/><stop offset=".55" stop-color="#24502c"/><stop offset=".75" stop-color="#2d9ec4"/><stop offset="1" stop-color="#1f7fa8"/></linearGradient></defs><rect width="227" height="420" fill="url(#f2)"/></svg>
    <div class="text"><h3>Elegant Design</h3><p>Our pools come in a variety of styles and finishes, seamlessly blending into any garden setting.</p></div>
  </div>
  <div class="feature">
    <svg class="photo" role="img" aria-label="Sea-view pool with clear turquoise water" viewBox="0 0 227 420" preserveAspectRatio="none"><defs><linearGradient id="f3" x1="0" y1="0" x2="0" y2="1"><stop offset="0" stop-color="#8bdbe6"/><stop offset=".45" stop-color="#6fcfdc"/><stop offset=".7" stop-color="#4fbec8"/><stop offset="1" stop-color="#8a7a6a"/></linearGradient></defs><rect width="227" height="420" fill="url(#f3)"/></svg>
    <div class="text"><h3>Custom and Tailor-Made</h3><p>Create the pool of your dreams with our customization options, tailored to your specific tastes and needs.</p></div>
  </div>
  <div class="feature">
    <svg class="photo" role="img" aria-label="Pool with a pavilion below wooded hills" viewBox="0 0 227 420" preserveAspectRatio="none"><defs><linearGradient id="f4" x1="0" y1="0" x2="0" y2="1"><stop offset="0" stop-color="#c9d2d6"/><stop offset=".25" stop-color="#4c7a3c"/><stop offset=".6" stop-color="#2f6a2c"/><stop offset=".8" stop-color="#2f8fe0"/><stop offset="1" stop-color="#4a8a30"/></linearGradient></defs><rect width="227" height="420" fill="url(#f4)"/></svg>
    <div class="text"><h3>Easy Installation</h3><p>Enjoy your new oasis quickly with our simple and fast installation process.</p></div>
  </div>
  <div class="feature">
    <svg class="photo" role="img" aria-label="Seaside infinity pool under a bright sky" viewBox="0 0 227 420" preserveAspectRatio="none"><defs><linearGradient id="f5" x1="0" y1="0" x2="0" y2="1"><stop offset="0" stop-color="#1ea8d8"/><stop offset=".45" stop-color="#8fd6ea"/><stop offset=".65" stop-color="#23a6c0"/><stop offset="1" stop-color="#5fb8c0"/></linearGradient></defs><rect width="227" height="420" fill="url(#f5)"/></svg>
    <div class="text"><h3>Constant Innovation</h3><p>We incorporate the latest technologies to provide you with an optimal and safe swimming experience.</p></div>
  </div>
</section>

<section class="split reverse block">
  <div class="copy">
    <h2>Personalized Services</h2>
    <p class="body-text">We understand that every garden and client is unique. That's why we offer personalized services, from design to installation and after-sales support. Our team of experts is here to answer all your questions and guide you throughout your project.</p>
  </div>
  <div class="media">
    <svg class="photo" role="img" aria-label="Infinity pool with pergola facing the sea" viewBox="0 0 693 333" preserveAspectRatio="none"><defs><linearGradient id="b1" x1="0" y1="0" x2="0" y2="1"><stop offset="0" stop-color="#7cc7ec"/><stop offset=".5" stop-color="#3aa9cc"/><stop offset=".7" stop-color="#d6c8a8"/><stop offset="1" stop-color="#0d8fc6"/></linearGradient></defs><rect width="693" height="333" fill="url(#b1)"/></svg>
  </div>
</section>

<section class="split block">
  <div class="media">
    <svg class="photo" role="img" aria-label="Courtyard pool seen from above with plants and loungers" viewBox="0 0 694 333" preserveAspectRatio="none"><defs><linearGradient id="b2" x1="0" y1="0" x2="1" y2="1"><stop offset="0" stop-color="#8a8f7a"/><stop offset=".35" stop-color="#c8c3b4"/><stop offset=".6" stop-color="#3fd0e6"/><stop offset="1" stop-color="#5a7a3a"/></linearGradient></defs><rect width="694" height="333" fill="url(#b2)"/></svg>
  </div>
  <div class="copy">
    <h2>Guaranteed Satisfaction</h2>
    <p class="body-text">Your satisfaction is our top priority. We are committed to providing you with exceptional service and the highest quality products. Join our community of satisfied customers who are already enjoying their custom above-ground pools. <strong>10-Year Warranty!</strong></p>
  </div>
</section>

<section class="split reverse block">
  <div class="copy">
    <h2>Contact Us Today</h2>
    <p class="body-text">Don't wait any longer to transform your garden into a wellness oasis. Contact us today to discover our range of customizable above-ground pools and get a tailored quote. Dive into a world of infinite possibilities with Brisa Lagoon.</p>
    <a class="button" href="#">Contact Us</a>
  </div>
  <div class="media">
    <svg class="photo" role="img" aria-label="Ocean pool beside a seaside building" viewBox="0 0 693 333" preserveAspectRatio="none"><defs><linearGradient id="b3" x1="0" y1="0" x2="0" y2="1"><stop offset="0" stop-color="#5fb6e4"/><stop offset=".25" stop-color="#1d6c9a"/><stop offset=".7" stop-color="#1a7fa8"/><stop offset="1" stop-color="#27b2b0"/></linearGradient></defs><rect width="693" height="333" fill="url(#b3)"/></svg>
  </div>
</section>

<footer class="site-footer">
  <div class="brand"><span>BRISA</span><span>LAGOON</span></div>
  <p class="tagline">We Bring Your Pool Dreams to Life!</p>
  <div class="socials">
    <span aria-label="Social profile"></span><span aria-label="Social profile"></span><span aria-label="Social profile"></span><span aria-label="Social profile"></span>
  </div>
</footer>
<div class="copyright">Copyright © 2024 Brisa Lagoon | All rights reserved.</div>

</body>
</html>
```